NZ First of it's kind solutions directory and marketplace for busy Mums needs a business card design

We need a business card design for our new nationwide business in NZ (long term plans to go global). We provide solutions to the everyday challenges that busy Mums face by connecting them with quality communities and suppliers of carefully selected, relevant products and services. We sell direct via our online marketplace. The final design should communicate our values of inclusivity, quality and smart solutions. Colours should incorporate our logo colour palette of #477077 and #6ba8b2. Our website is at https://www.brightnestmums.example

Target Market(s)

busy Mums, Age 28 – 50, female, income over $100K, location main centres NZ primarily but NZ wide. Is likely juggling work or career with a young family. Probably had hobbies which have fallen by the wayside.
-Wants to succeed in her chosen career without compromising on family life
-to successfully juggle her career without feeling like she is compromising her children
- Is time poor, something always has to give and it’s generally her health (she’ll stay up late, get stressed)
- probably ex corporate or professional career. Has discretional income

Industry/Entity Type

Business

Contact Information for Business Card

Lena Forbisher, Founder, BrightNestMums.example (Strapline Tap; Gather; Sorted), 47 Kowhai Terrace, Ellerslie, Auckland 1051, New Zealand. Mob: 021 483 517 Ph: +64 (0)9 571 4860

Font styles to use
Other font styles liked:
• Raleway, and/or Architects Daughter

Colors
00a990
33b8a4
86cfc6
cfeae6

Requirements
Must have
• the above details, streamline. the logo and colours associated with those logos
Should not have
• foil or metallic colours

```html
<!DOCTYPE html>
<html lang="en">
<head>
<meta charset="utf-8">
<title>BrightNestMums – Business Card</title>
<link href="https://fonts.googleapis.com/css2?family=Roboto:wght@400;700&family=Roboto+Condensed:wght@400;700&display=swap" rel="stylesheet">
<style>
  :root {
    --teal-deep: #477077;
    --teal-light: #6ba8b2;
    --paper: #fbfbfa;
    --ink: #4a4f52;
    --rule: #b9bfc1;
    --stage: #e9ecec;
  }
  * { box-sizing: border-box; margin: 0; padding: 0; }
  html, body { width: 1200px; height: 886px; overflow: hidden; }
  body {
    background: var(--stage);
    font-family: "Roboto", Arial, sans-serif;
    position: relative;
  }
  .card {
    position: absolute;
    top: 288px;
    width: 540px;
    height: 309px;
    overflow: hidden;
    box-shadow: 0 6px 18px rgba(0,0,0,0.18);
  }
  /* Front */
  .card-front { left: 40px; background: var(--paper); }
  .brand {
    position: absolute; left: 196px; top: 56px;
    display: flex; align-items: center; gap: 10px;
  }
  .brand-dot {
    width: 26px; height: 26px; border-radius: 50%;
    background: var(--teal-deep);
  }
  .brand-name {
    font-weight: 700; font-size: 30px; letter-spacing: -0.5px;
    color: var(--teal-deep);
  }
  .divider {
    position: absolute; left: 150px; right: 40px; top: 124px;
    height: 1px; background: var(--rule);
  }
  .person { position: absolute; left: 36px; top: 166px; }
  .person-name {
    font-family: "Roboto Condensed", Arial, sans-serif;
    font-weight: 700; font-size: 20px; color: var(--teal-deep);
    letter-spacing: 0.2px;
  }
  .person-role {
    font-family: "Roboto Condensed", Arial, sans-serif;
    font-size: 14px; color: var(--teal-light); margin-top: 1px;
  }
  .contacts { position: absolute; left: 36px; top: 216px; list-style: none; }
  .contacts li {
    display: flex; align-items: center; gap: 8px;
    font-size: 12px; color: var(--ink); line-height: 17px;
  }
  .contacts svg { width: 10px; height: 10px; fill: var(--ink); }
  .address {
    position: absolute; right: 40px; top: 150px; text-align: right;
    font-size: 12.5px; line-height: 17px; color: var(--ink);
  }
  .band { position: absolute; left: 0; bottom: 0; width: 540px; height: 50px; }
  .strapline {
    position: absolute; right: 24px; bottom: 10px;
    font-family: "Roboto Condensed", Arial, sans-serif;
    font-size: 12px; letter-spacing: 0.6px; color: #fff;
    text-transform: uppercase;
  }
  /* Back */
  .card-back { left: 620px; background: var(--teal-deep); }
  .back-mark {
    position: absolute; right: 70px; top: 44px;
    width: 130px; height: 130px; border-radius: 50%;
    background: #f4f6f6;
  }
  .back-name {
    position: absolute; left: 40px; bottom: 40px;
    font-weight: 700; font-size: 48px; letter-spacing: -1px;
    color: var(--teal-light);
  }
</style>
</head>
<body>
  <section class="card card-front" aria-label="Business card front">
    <div class="brand">
      <span class="brand-dot"></span>
      <span class="brand-name">BrightNestMums</span>
    </div>
    <div class="divider"></div>

    <div class="person">
      <p class="person-name">LENA FORBISHER</p>
      <p class="person-role">FOUNDER</p>
    </div>

    <ul class="contacts">
      <li>
        <svg viewBox="0 0 10 10"><path d="M2 0.5l2 2-1 1.2c.6 1.3 1.5 2.2 2.8 2.8L7 5.5l2 2L7.8 9.5C4 9 1 6 0.5 2.2z"/></svg>
        +64 (0)9 571 4860
      </li>
      <li>
        <svg viewBox="0 0 10 10"><path d="M2.5 0h5v10h-5zM3.3 1v7h3.4V1z"/></svg>
        021 483 517
      </li>
      <li>
        <svg viewBox="0 0 10 10"><circle cx="5" cy="5" r="5"/><path d="M0 5h10M5 0v10" stroke="#fbfbfa" stroke-width="0.8"/></svg>
        BrightNestMums.example
      </li>
    </ul>

    <address class="address" style="font-style:normal">
      47 Kowhai Terrace, Ellerslie<br>
      Auckland 1051, New Zealand
    </address>

    <svg class="band" viewBox="0 0 540 50" aria-hidden="true">
      <rect x="0" y="36" width="34" height="14" fill="var(--teal-deep)"/>
      <rect x="34" y="43" width="506" height="7" fill="var(--teal-light)"/>
      <path d="M300 50 L300 40 Q300 16 324 16 L540 16 L540 50 Z" fill="var(--teal-light)"/>
      <path d="M296 41 Q296 12 326 12 L540 12" fill="none" stroke="var(--teal-light)" stroke-width="1.2" opacity="0.6"/>
    </svg>
    <p class="strapline">Tap; Gather; Sorted</p>
  </section>

  <section class="card card-back" aria-label="Business card back">
    <div class="back-mark"></div>
    <p class="back-name">BrightNestMums</p>
  </section>
</body>
</html>
```